A Techincal Author needs a site to promote his Programming Books

The StudyAlong series is a collection of books focusing on building the same app with different technologies. The purpose of this project is to design a web site home page that can be used to sell the books.

Expected Deliverables
• StudyAlong Logo as Illustrator file
• Master graphic design files for any relevant web assets
• HTML and CSS for home page, if applicable

Target Market(s)

The target market for our series is web programmers. They are people who have some experience, but want to learn a new tool. Programmers are analytical, logical people who like structure in the things they do.

Here are some things our customers like:

• Chirply / Postbox
• Crown of Ashes / Hollow Tide / Salt Hollow
• SmartPhones, Tablets, Stridelets, and other tech gadgets.

The design should try to speak to that market.

Requirements
Must have
• The primary tasks for this project are:
• 1) Create "Study Along" Logo.
• * All “NetPivot” properties use a similar logo approach, with the NetPivot ball icon on the left, a reflection below it. The company name is on the right, roughly the same size as the ball icon. A tag line underneath the company name, roughly the same size as the reflection.
• * Company Name: Study Along
• * Tagline: Knowledge to Boost Your Career
• * Logo color is up to the discretion of the designer, but should be compatible with the site design.
• * Sample Logos for other NetPivot properties in Illustrator format are available as attachments to this project.
• 2) Design the Study Along Home Page.
• The home page should follow this format:
• * Logo
• * Nav Bar
• • Buy (The Home Page)
• • About
• • Contact
• * Main Content
• • Home page content detailed in attachment
• * Footer
• • Copyright notice
• • Links to other stuff we do ( net-pivot.example | marlonpeake.example | BeyondTheGrid.example )
Nice to have
• It would be nice to have a book as part of the home page content.
Should not have
• Please do not use the same color scheme as BeyondTheGrid.example or Plumvane.example or QueryTheMaven.example

```html
<!DOCTYPE html>
<html lang="en">
<head>
<meta charset="utf-8">
<title>Study Along</title>
<link rel="stylesheet" href="https://fonts.googleapis.com/css2?family=Roboto:wght@400;500;700&family=Open+Sans:wght@400;600;700&display=swap">
<style>
:root{
  --ink:#333333;
  --dark:#555555;
  --btn:#3d3d3d;
  --cell:#f1f1f1;
  --line:#d6d6d6;
  --coral:#ff6b6b;
  --amber:#ffa000;
  --band:#f6f6f6;
  --footer:#000000;
  --white:#ffffff;
}
*{box-sizing:border-box;margin:0;padding:0}
html,body{width:1200px;height:2311px;overflow:hidden;background:var(--white)}
body{position:relative;font-family:"Roboto",Arial,sans-serif;color:var(--ink)}
.abs{position:absolute}

/* header */
.site-header{left:0;top:0;width:1200px;height:78px}
.brand{left:155px;top:16px;font-size:37px;font-weight:400;color:var(--ink)}
.main-nav{right:132px;top:29px;display:flex;gap:32px;font-size:14px}
.main-nav span{color:var(--ink)}

/* hero */
.hero{left:0;top:78px;width:1200px;height:512px;overflow:hidden}
.hero-photo{position:absolute;inset:0;background:linear-gradient(90deg,#f4f4f4 0%,#eeeeee 38%,#cfd6dc 55%,#9fb3c4 72%,#3d9c98 86%,#2f7c88 100%)}
.hero-title{left:155px;top:117px;font-size:36px;line-height:44px;font-weight:400;color:#3a3a3a;letter-spacing:.5px}
.signup{left:155px;top:219px;width:440px;height:220px}
.signup svg{position:absolute;inset:0}
.signup h2{position:absolute;left:0;width:370px;top:18px;text-align:center;font-size:17px;font-weight:400;color:#3a3a3a}
.field{position:absolute;left:51px;width:290px;height:32px;border-radius:16px;background:var(--white);font-size:11px;color:#666;padding:9px 0 0 23px}
.submit{position:absolute;left:51px;top:142px;width:290px;height:32px;border-radius:16px;background:var(--btn);color:var(--white);font-size:14px;text-align:center;line-height:32px}
.slider-arrows{left:977px;top:476px}

/* welcome */
.welcome-title{left:0;width:1200px;top:626px;text-align:center;font-size:25px;font-weight:700;letter-spacing:.5px;color:#333}
.welcome-text{left:170px;width:860px;top:668px;text-align:center;font-family:"Open Sans",Arial,sans-serif;font-size:12.5px;line-height:20px;color:#333}

/* book sections */
.book-title{left:0;width:1200px;text-align:center;font-family:"Open Sans",Arial,sans-serif;font-size:26px;font-weight:400;color:#333}
.app-link{left:546px;width:110px;height:29px;border-radius:15px;background:var(--btn);color:var(--white);font-family:"Open Sans",Arial,sans-serif;font-size:10px;font-weight:700;text-align:center;line-height:29px}
.price-table{left:221px;width:758px;font-family:"Open Sans",Arial,sans-serif}
.price-row{display:flex;height:49px;border-bottom:1px solid var(--line)}
.price-row .label{width:251px;background:var(--dark);color:var(--white);font-size:14px;font-weight:700;padding-left:28px;display:flex;align-items:center;border-bottom:1px solid #444}
.price-row .price{width:256px;background:var(--cell);font-size:23px;font-weight:700;color:#333;display:flex;align-items:center;justify-content:center}
.price-row .buy{width:124px;background:var(--coral);color:var(--white);font-size:11px;font-weight:700;display:flex;align-items:center;justify-content:center}
.price-row .store{width:127px;background:var(--amber);color:var(--white);font-size:11px;font-weight:700;line-height:19px;display:flex;align-items:center;justify-content:center;text-align:center;border-bottom:1px solid #e08c00}
.price-row .store.empty{background:var(--cell);border-bottom:none}

/* partners */
.partners{left:0;top:1670px;width:1200px;height:112px;background:var(--band);display:flex;align-items:center;justify-content:center;gap:90px}
.partner{font-family:"Roboto",Arial,sans-serif;font-size:28px;font-weight:400;color:var(--ink)}

/* contact */
.contact-title{left:0;width:1200px;top:1808px;text-align:center;font-size:30px;font-weight:400;color:#111}
.input{position:absolute;background:#f7f7f7;font-size:10px;color:#555;padding:13px 0 0 16px}
.send{left:530px;top:2055px;width:140px;height:40px;border-radius:20px;background:var(--btn);color:var(--white);font-size:10px;font-weight:700;text-align:center;line-height:40px}
.social{top:2115px;left:499px;display:flex;gap:15px}
.social span{width:59px;height:59px;border:2px solid #111;border-radius:50%;display:flex;align-items:center;justify-content:center;font-size:9px;font-weight:500;color:#111}

/* footer */
.site-footer{left:0;top:2205px;width:1200px;height:106px;background:var(--footer);color:var(--white)}
.footer-nav{position:absolute;left:0;width:1200px;top:30px;display:flex;justify-content:center;gap:26px;font-size:12px}
.copyright{position:absolute;left:0;width:1200px;top:66px;text-align:center;font-size:10px}
</style>
</head>
<body>

<header class="site-header abs">
  <div class="brand abs">Study-Along</div>
  <nav class="main-nav abs">
    <span>HOME</span><span>ABOUT US</span><span>SERVICES</span><span>BLOG</span><span>PRICING</span><span>CONTACT</span>
  </nav>
</header>

<section class="hero abs">
  <div class="hero-photo" role="img" aria-label="Three young developers gathered around a desktop monitor in a bright office"></div>
  <h1 class="hero-title abs">KNOWLEDGE TO<br>BOOST YOUR CAREER</h1>
  <div class="signup abs">
    <svg width="440" height="220" viewBox="0 0 440 220"><polygon points="0,0 440,0 370,70 370,220 0,220" fill="rgba(218,218,220,0.93)"/></svg>
    <h2>SIGN UP FOR A FREE SAMPLE</h2>
    <div class="field" style="top:52px">First Name</div>
    <div class="field" style="top:96px">Email Address</div>
    <div class="submit">SUBMIT</div>
  </div>
  <svg class="slider-arrows abs" width="34" height="16" viewBox="0 0 34 16">
    <path d="M2 8h12M2 8l5-5M2 8l5 5" stroke="#111" stroke-width="2.4" fill="none"/>
    <path d="M32 8H20M32 8l-5-5M32 8l-5 5" stroke="#111" stroke-width="2.4" fill="none"/>
  </svg>
</section>

<h2 class="welcome-title abs">WELCOME TO STUDY ALONG</h2>
<p class="welcome-text abs">Duis aute irure dolor in reprehenderit in voluptate velit esse cillum dolore eu fugiat nulla pariatur. Excepteur sint occaecat cupidatat non proident, sunt in culpa qui officia deserunt mollit anim id est laborum.</p>

<h3 class="book-title abs" style="top:723px">AnvilJS 1.5 &amp; Scaffold</h3>
<div class="app-link abs" style="top:768px">View App Link</div>
<div class="price-table abs" style="top:821px">
  <div class="price-row"><div class="label">With Mock Services</div><div class="price">$5.99</div><div class="buy">Buy From Us</div><div class="store">Buy From<br>Riverstore</div></div>
  <div class="price-row"><div class="label">With NexusJS Services</div><div class="price">$5.99</div><div class="buy">Buy From Us</div><div class="store">Buy From<br>Riverstore</div></div>
  <div class="price-row"><div class="label">With FrostForge Services</div><div class="price">$5.99</div><div class="buy">Buy From Us</div><div class="store">Buy From<br>Riverstore</div></div>
  <div class="price-row"><div class="label">Buy Them All</div><div class="price">$9.99</div><div class="buy">Buy From Us</div><div class="store empty"></div></div>
</div>

<h3 class="book-title abs" style="top:1036px">AnvilJS 2 &amp; Scaffold</h3>
<div class="app-link abs" style="top:1081px">View App Link</div>
<div class="price-table abs" style="top:1134px">
  <div class="price-row"><div class="label">With Mock Services</div><div class="price">$5.99</div><div class="buy">Buy From Us</div><div class="store">Buy From<br>Riverstore</div></div>
  <div class="price-row"><div class="label">With NexusJS Services</div><div class="price">$5.99</div><div class="buy">Buy From Us</div><div class="store">Buy From<br>Riverstore</div></div>
  <div class="price-row"><div class="label">With FrostForge Services</div><div class="price">$5.99</div><div class="buy">Buy From Us</div><div class="store">Buy From<br>Riverstore</div></div>
  <div class="price-row"><div class="label">Buy Them All</div><div class="price">$9.99</div><div class="buy">Buy From Us</div><div class="store empty"></div></div>
</div>

<h3 class="book-title abs" style="top:1349px">RippleJS</h3>
<div class="app-link abs" style="top:1394px">View App Link</div>
<div class="price-table abs" style="top:1447px">
  <div class="price-row"><div class="label">With Mock Services</div><div class="price">$5.99</div><div class="buy">Buy From Us</div><div class="store">Buy From<br>Riverstore</div></div>
  <div class="price-row"><div class="label">With NexusJS Services</div><div class="price">$5.99</div><div class="buy">Buy From Us</div><div class="store">Buy From<br>Riverstore</div></div>
  <div class="price-row"><div class="label">With FrostForge Services</div><div class="price">$5.99</div><div class="buy">Buy From Us</div><div class="store">Buy From<br>Riverstore</div></div>
  <div class="price-row"><div class="label">Buy Them All</div><div class="price">$9.99</div><div class="buy">Buy From Us</div><div class="store empty"></div></div>
</div>

<section class="partners abs">
  <div class="partner">Plumvane</div>
  <div class="partner">Beyond The Grid</div>
</section>

<h2 class="contact-title abs">CONTACT US</h2>
<div class="input" style="left:340px;top:1870px;width:256px;height:36px">Name</div>
<div class="input" style="left:607px;top:1870px;width:258px;height:36px">Email</div>
<div class="input" style="left:340px;top:1914px;width:525px;height:36px">Subject</div>
<div class="input" style="left:340px;top:1958px;width:525px;height:78px">Message</div>
<div class="send abs">SEND MESSAGE</div>
<div class="social abs"><span>Pagebook</span><span>Chirply</span><span>Linkly</span></div>

<footer class="site-footer abs">
  <nav class="footer-nav"><span>HOME</span><span>ABOUT US</span><span>SERVICES</span><span>BLOG</span><span>PRICING</span><span>CONTACT</span></nav>
  <div class="copyright">© 2016, www.studyalong.example</div>
</footer>

</body>
</html>
```